Detail Shop Business card design

i need a business card design for my new detailing company called 'Brisk's Polish Works'. i want an all black and white design . simple, direct and to the point. i want the designer to choose a fitting font to match the logothe front should have logo, address, phone and email and the back side should have a slogan and text indicating that we offer services on anything including cars, trucks, motorcycles and RVs. slogan will read "we take pride in your ride"
maybe also very small on the back side the IG icon with Brisks_Polish_Works

phone 208.417.6352
address 3847 E Larkin Ave
Spokane WA 99214
email: BrisksPolish@mailvexo.com

Target Market(s)

all ages , auto enthusiasts

Industry/Entity Type

Automotive

Contact Information for Business Card

the front should have logo, address, phone and email and the back side should have a slogan and text indicating that we offer services on anything including cars, trucks, motorcycles and RVs. slogan will read "we take pride in your ride"

phone 208.417.6352
address 3847 E Larkin Ave
Spokane WA 99214

Colors
000000
ffffff

Requirements
Must have
• bold font and very simple design with good spacing
Nice to have
• anything creative from the designer indicating we service any types of vehicles
Should not have
• any colors ,

```html
<!DOCTYPE html>
<html lang="en">
<head>
<meta charset="utf-8">
<title>Brisk's Polish Works – Business Card</title>
<link rel="stylesheet" href="https://fonts.googleapis.com/css2?family=Roboto+Slab:wght@400;700&family=Archivo:wght@400;500&display=swap">
<style>
  :root {
    --ink: #000000;
    --paper: #ffffff;
    --card-white: #f7f7f7;
    --backdrop: #5a5a5a;
    --muted-light: #e6e6e6;
  }
  * { box-sizing: border-box; margin: 0; padding: 0; }
  html, body {
    width: 1200px;
    height: 900px;
    overflow: hidden;
    background: var(--backdrop);
  }
  .canvas {
    position: relative;
    width: 1200px;
    height: 900px;
  }
  .card {
    position: absolute;
    width: 620px;
    height: 354px;
    border-radius: 26px;
    overflow: hidden;
  }

  /* Back side */
  .card--back {
    left: 90px;
    top: 70px;
    background: var(--ink);
    color: var(--paper);
    display: flex;
    flex-direction: column;
    align-items: center;
    justify-content: center;
  }
  .brand {
    display: flex;
    align-items: center;
    gap: 12px;
    font-family: "Roboto Slab", serif;
    font-weight: 700;
    font-size: 30px;
    letter-spacing: 0.5px;
  }
  .brand__dot {
    width: 22px;
    height: 22px;
    border-radius: 50%;
    background: currentColor;
    flex: none;
  }
  .card--back .brand { margin-bottom: 26px; }
  .slogan {
    font-family: "Archivo", sans-serif;
    font-weight: 500;
    font-size: 19px;
    letter-spacing: 0.3px;
  }
  .social {
    display: flex;
    flex-direction: column;
    align-items: center;
    gap: 6px;
    margin-top: 12px;
    font-family: "Archivo", sans-serif;
    font-size: 13px;
    color: var(--muted-light);
  }
  .social__mark {
    width: 14px;
    height: 14px;
    border: 2px solid var(--paper);
    border-radius: 3px;
  }

  /* Front side */
  .card--front {
    left: 490px;
    top: 470px;
    background: var(--card-white);
    color: var(--ink);
  }
  .card--front .brand {
    position: absolute;
    left: 60px;
    top: 132px;
    font-size: 26px;
  }
  .contact {
    position: absolute;
    left: 320px;
    top: 58px;
    font-family: "Roboto Slab", serif;
    font-size: 15px;
    line-height: 1.55;
    list-style: none;
  }
  .contact__row { display: flex; gap: 6px; }
  .contact__label { width: 26px; flex: none; }
  .band {
    position: absolute;
    left: 0;
    right: 0;
    background: var(--ink);
  }
  .band--slogan {
    top: 226px;
    height: 50px;
    display: flex;
    align-items: center;
    justify-content: center;
    color: var(--paper);
  }
  .band--slogan .slogan { font-size: 16px; }
  .band--base {
    top: 284px;
    height: 22px;
  }
</style>
</head>
<body>
<main class="canvas">

  <section class="card card--back" aria-label="Card back">
    <div class="brand"><span class="brand__dot"></span><span>Brisk's Polish Works</span></div>
    <p class="slogan">We Take Pride In Your Ride</p>
    <div class="social">
      <span class="social__mark"></span>
      <span>Brisks_Polish_Works</span>
    </div>
  </section>

  <section class="card card--front" aria-label="Card front">
    <div class="brand"><span class="brand__dot"></span><span>Brisk's Polish Works</span></div>
    <ul class="contact">
      <li class="contact__row"><span class="contact__label">P :</span><span>208.417.6352</span></li>
      <li class="contact__row"><span class="contact__label">M :</span><span>BrisksPolish@mailvexo.com</span></li>
      <li class="contact__row"><span class="contact__label">A :</span><span>3847 E Larkin Ave<br>Spokane WA 99214</span></li>
    </ul>
    <div class="band band--slogan"><p class="slogan">We Take Pride In Your Ride</p></div>
    <div class="band band--base"></div>
  </section>

</main>
</body>
</html>
```